super clean and modern easy to read. Scandinavian type design.

Hi everyone, we need a wall menu for our retail space. We'd like something that goes along with the style of our website and is also editable (in case we change prices later on). The dimensions for the menu will be about 72 inches wide and about 48 inches high and it will be attached to the wall in our business. Please pull menu wording from this link: http://www.brivelounge.com/services

Feel free to shorten the descriptions.

The main sections of the menu are:
mod facials
enhancements
add-ons ($15, $20, and $30)
celebrity facials

Please include the picture of the woman on our homepage in the menu. I'll attach an image.

We would like to start with our process to simplify the steps we take.
1.)Complimentary skin analysis
2.) Choose your service
3.) Choose your products (recommendations are given)
4.) Enjoy!
5.) Further your results with take home products

Last little note, we can email you a larger Logo...Pixel Harbor would not let us upload the largest file that we have for the logo.

Target Market(s)

young, fun, hip, suburban women and men.

Industry/Entity Type

Retail

Font styles to use
Sans Serif

Requirements
Must have
• Not too much orange. Keep it clean and not too busy.
• the menu should make it super easy for someone to walk into the store and figure out the process.
• the 5 steps should be listed out first
• the 2 basic facials
• the add ons
• the enhancements (by price)
• the celebrity facials
• Advanced peels
• colors should be mainly blue and white (website) some orange used for framing categories or black. I like clean and not too busy. no cheesy.
Nice to have
• see colors on website. see style.
Should not have
• no clip art! no cursive formal writing.

```html
<!DOCTYPE html>
<html lang="en">
<head>
<meta charset="utf-8">
<title>brive lounge — wall menu</title>
<link href="https://fonts.googleapis.com/css2?family=Arimo:wght@400;700&family=Roboto+Condensed:wght@400;700&family=Roboto:wght@500;700&display=swap" rel="stylesheet">
<style>
  :root {
    --teal: #5bc4d1;
    --teal-light: #8fd3dd;
    --teal-wash: #dff2f5;
    --orange: #ef8a1f;
    --orange-light: #f8c596;
    --ink: #1f1f1f;
    --ink-soft: #333;
    --tab-grey: #6b6c6f;
    --white: #ffffff;
  }
  * { box-sizing: border-box; margin: 0; padding: 0; }
  html, body { width: 1200px; height: 800px; overflow: hidden; background: var(--white); }
  body { font-family: "Arimo", Arial, sans-serif; color: var(--ink); position: relative; }

  .menu { position: absolute; inset: 0; background: linear-gradient(90deg, var(--white) 0%, var(--white) 74%, var(--teal-wash) 100%); }

  /* process band */
  .process { position: absolute; left: 0; top: 0; width: 1200px; height: 129px; background: var(--teal); }
  .step { position: absolute; top: 0; height: 129px; display: flex; align-items: center; gap: 10px; }
  .step-num { width: 62px; height: 62px; border-radius: 50%; background: var(--orange); color: var(--white);
    font: 700 40px/62px "Roboto Condensed", sans-serif; text-align: center; flex: none; box-shadow: 0 2px 4px rgba(0,0,0,.25); }
  .step-label { font: 400 30px/33px "Roboto Condensed", sans-serif; color: var(--white); letter-spacing: -.3px; }
  .step-label small { font-size: 15px; line-height: 13px; display: inline-block; vertical-align: -2px; text-align: center; }
  .step-1 { left: 18px; } .step-2 { left: 240px; } .step-3 { left: 486px; } .step-4 { left: 723px; } .step-5 { left: 883px; }

  /* section heads */
  .section-title { font: 700 37px/40px "Roboto", sans-serif; color: var(--teal); letter-spacing: -.5px;
    display: inline-flex; align-items: center; gap: 8px; padding-bottom: 4px; border-bottom: 2px dashed var(--orange); }
  .dots { display: inline-flex; gap: 3px; }
  .dots i { width: 20px; height: 20px; border-radius: 50%; background: var(--orange); display: block; }

  /* facials */
  .facials { position: absolute; left: 35px; top: 150px; width: 300px; }
  .facial-name { font: 700 16px/20px "Arimo", sans-serif; color: var(--teal); margin-top: 10px; }
  .facials ul { list-style: none; font-size: 12.3px; line-height: 13.6px; }
  .facials li { padding-left: 9px; position: relative; }
  .facials li::before, .menu-list li::before { content: "•"; position: absolute; left: 0; }
  .series { font-weight: 700; font-size: 13.5px; margin: 3px 0 0 9px; }

  /* enhancements */
  .enhancements { position: absolute; left: 388px; top: 150px; }
  .menu-list { list-style: none; }
  .menu-list li { position: relative; padding-left: 9px; }
  .enhancements .menu-list { margin: 12px 0 0 50px; font-size: 14.3px; line-height: 17.5px; color: var(--ink-soft); }
  .enhancements .menu-list li { margin-bottom: 3px; }
  .menu-list b { color: var(--ink); }

  .arrow { position: absolute; }
  .arrow-1 { left: 305px; top: 232px; }
  .arrow-2 { left: 668px; top: 242px; }

  /* brand */
  .brand-rule { position: absolute; left: 343px; width: 420px; height: 2px; background: var(--teal); }
  .brand-rule.top { top: 398px; }
  .brand-rule.bottom { top: 538px; }
  .brand { position: absolute; left: 343px; top: 420px; width: 420px; text-align: center;
    font: 700 74px/96px "Roboto", sans-serif; color: var(--teal); letter-spacing: -3px; }
  .social { position: absolute; top: 527px; left: 515px; display: flex; gap: 9px; background: var(--white); padding: 0 6px; }
  .social span { width: 22px; height: 22px; border-radius: 50%; background: var(--teal); display: block; }

  /* add-ons */
  .addons { position: absolute; left: 815px; width: 380px; }
  .addons .menu-list { margin: 10px 0 0 0; font-size: 14px; line-height: 16px; color: var(--ink-soft); }
  .addons .menu-list li { margin-bottom: 3px; }
  .addons-15 { top: 152px; } .addons-20 { top: 345px; } .addons-30 { top: 468px; }
  .addons-30 .menu-list { font-size: 13.6px; line-height: 15.6px; }
  .addons-30 .menu-list li { margin-bottom: 2px; }

  /* featured */
  .featured { position: absolute; left: 39px; top: 563px; width: 744px; height: 207px; background: var(--teal-light);
    box-shadow: 2px 3px 5px rgba(0,0,0,.3); }
  .featured-tab { position: absolute; left: 0; top: 0; width: 302px; height: 45px; background: var(--tab-grey);
    color: var(--white); font: italic 700 29px/45px "Roboto Condensed", sans-serif; padding-left: 12px; letter-spacing: -.5px; }
  .celebrity-title { position: absolute; left: 318px; top: 4px; font: 700 34px/42px "Roboto", sans-serif; color: var(--white);
    letter-spacing: -.5px; border-bottom: 2px dashed var(--orange); padding-right: 4px; display: flex; align-items: center; gap: 6px;
    text-shadow: 0 1px 2px rgba(0,0,0,.25); }
  .celebrity-title svg { display: block; }
  .treatment { position: absolute; top: 64px; color: var(--ink); }
  .treatment h3 { font: 700 14.3px/16px "Arimo", sans-serif; }
  .treatment .tagline { font-size: 14px; line-height: 15px; }
  .treatment p { font-size: 10.5px; line-height: 12.5px; margin-top: 2px; }
  .t-oxygen { left: 27px; width: 130px; }
  .t-led { left: 210px; width: 140px; }
  .t-lift { left: 372px; width: 165px; }
  .t-peel { left: 562px; width: 178px; }
  .t-peel h3 + p { margin-bottom: 14px; }
  .divider { position: absolute; top: 66px; width: 2px; height: 120px; background: var(--orange); }
  .d1 { left: 193px; } .d2 { left: 356px; } .d3 { left: 540px; }
</style>
</head>
<body>
<main class="menu">

  <header class="process">
    <div class="step step-1"><span class="step-num">1.</span><span class="step-label">choose your<br>facial</span></div>
    <div class="step step-2"><span class="step-num">2.</span><span class="step-label">complimentary<br>skin analysis</span></div>
    <div class="step step-3"><span class="step-num">3.</span><span class="step-label">choose<br>enhancement<br>products <small>(advice<br>given)</small></span></div>
    <div class="step step-4"><span class="step-num">4.</span><span class="step-label">relax +<br>enjoy!</span></div>
    <div class="step step-5"><span class="step-num">5.</span><span class="step-label">extend results with<br>take home products</span></div>
  </header>

  <section class="facials">
    <h2 class="section-title">brive facials <span class="dots"><i></i><i></i></span></h2>

    <h3 class="facial-name">brivefacial essential 30 min | $49</h3>
    <ul>
      <li>deep breathing with lavender essential oils</li>
      <li>includes In-depth skin analysis, with recommendations</li>
      <li>power cleanse x2, hot steam, exfoliation high frequency treatment or facial vacuum</li>
      <li>Shiatsu style massage</li>
      <li>lavender hot towel treatment</li>
      <li>customized mask, sun protection and lip treatment</li>
    </ul>
    <p class="series">Series of 3 $125</p>

    <h3 class="facial-name">brivefacial essential 45 min | $69</h3>
    <ul>
      <li>facial customized specifically for your skins needs</li>
      <li>deep cleansing, exfoliation and hydration</li>
      <li>may include a bubbling pore mask, a pore vacuum, high frequency, special hydration mask</li>
      <li>lymphatic draining facial and neck massage</li>
      <li>hand, arm and décolleté massage</li>
    </ul>
    <p class="series">Series of 3 $165</p>
  </section>

  <svg class="arrow arrow-1" width="128" height="104" viewBox="0 0 128 104" aria-hidden="true">
    <polygon points="0,24 74,24 74,0 128,50 74,104 74,78 0,78" fill="#ef8a1f"/>
    <polygon points="0,24 74,24 74,0 82,8 82,32 8,32" fill="#f8c596"/>
    <polygon points="8,32 82,32 82,8 118,50 82,92 82,70 8,70" fill="#f3a45b"/>
  </svg>

  <section class="enhancements">
    <h2 class="section-title">enhancements $10 <span class="dots"><i></i><i></i></span></h2>
    <ul class="menu-list">
      <li><b>vitamin c</b> (radiance + fine lines)</li>
      <li><b>peptide</b> (plump &amp; smooth)</li>
      <li><b>hyaluronic acid</b><br>(moisture.anti-aging)</li>
      <li><b>retinol</b> (fine lines.age spots)</li>
      <li><b>dehydrated eye treatment</b></li>
      <li><b>cherry enzyme peel</b><br>(antioxidant, healthy glow)</li>
      <li><b>pumpkin</b> (revitalizes, reduce lines)</li>
    </ul>
  </section>

  <svg class="arrow arrow-2" width="128" height="100" viewBox="0 0 128 104" aria-hidden="true">
    <polygon points="0,24 74,24 74,0 128,50 74,104 74,78 0,78" fill="#ef8a1f"/>
    <polygon points="0,24 74,24 74,0 82,8 82,32 8,32" fill="#f8c596"/>
    <polygon points="8,32 82,32 82,8 118,50 82,92 82,70 8,70" fill="#f3a45b"/>
  </svg>

  <div class="brand-rule top"></div>
  <div class="brand">brivelounge</div>
  <div class="brand-rule bottom"></div>
  <div class="social" aria-hidden="true"><span></span><span></span><span></span><span></span></div>

  <section class="addons addons-15">
    <h2 class="section-title">add-ons $15 <span class="dots"><i></i><i></i></span></h2>
    <ul class="menu-list">
      <li><b>wax - brow, chin or lip</b> (touch up)</li>
      <li><b>magnetic mud mask</b><br>(nourish.mineral infusion)</li>
      <li><b>peppermint/eucalyptus scalp massage</b><br>(invigorating.stress reduction)</li>
      <li><b>beard Oil Treatment</b><br>(softens and protects)</li>
    </ul>
  </section>

  <section class="addons addons-20">
    <h2 class="section-title">add-ons $20 <span class="dots"><i></i><i></i></span></h2>
    <ul class="menu-list">
      <li><b>me time - 20 min extra massage</b>(relax.enjoy)</li>
      <li><b>hand rejuvenation peel or microderm</b><br>(exfoliating, antiaging)</li>
    </ul>
  </section>

  <section class="addons addons-30">
    <h2 class="section-title">add-ons $30 <span class="dots"><i></i><i></i></span></h2>
    <ul class="menu-list">
      <li><b>crystal microdermabrasion for face and neck or declotte - 2 passes</b> (fine lines, smoothing)</li>
      <li><b>diamond microdermabrasion for face and neck or declotte - 2 passes</b> (fine lines, smoothing)</li>
      <li><b>led light therapy - 20 min</b> (red antiaging) (blue acne)</li>
      <li><b>decollete treatment</b><br>(peel or microderm) (anti-aging, fine lines)</li>
      <li><b>whole face wax</b> (except brows)</li>
      <li><b>hand treatment - peel + microderm</b><br>(double exfoliation for antiaging)</li>
      <li><b>facial hydration cocktail -1 pass of microderm + 7 advanced serums to fully hydrate your skin</b> (glow,renew)</li>
      <li><b>microcurrent eye, mouth, or chin</b> (non-surgical face lift)</li>
    </ul>
  </section>

  <section class="featured">
    <div class="featured-tab">for maximum results...</div>
    <h2 class="celebrity-title">celebrity facials
      <svg width="52" height="24" viewBox="0 0 52 24" aria-hidden="true">
        <polygon points="12,0 15,8 24,8 17,13 20,22 12,17 4,22 7,13 0,8 9,8" fill="#ef8a1f"/>
        <polygon points="38,0 41,8 50,8 43,13 46,22 38,17 30,22 33,13 26,8 35,8" fill="#ef8a1f"/>
      </svg>
    </h2>

    <article class="treatment t-oxygen">
      <h3>oxygen facial<br>50 min | $130</h3>
      <div class="tagline">(marisol vance's secret to red carpet skin)</div>
      <p>Rehydrates and plumps skin in less than an hour. naturally binds moisture within the skin for an instant glow.</p>
    </article>
    <div class="divider d1"></div>

    <article class="treatment t-led">
      <h3>led therapy facial<br>50 min | $130</h3>
      <div class="tagline">(Delia rowe's fav)</div>
      <p>We use LED for anti-aging, correcting discoloration, healing acne, and reversing the effects of sun damage. LED has been FDA approved for beauty treatments.</p>
    </article>
    <div class="divider d2"></div>

    <article class="treatment t-lift">
      <h3>Lumira Non Surgical Facelift| 50 min | $130</h3>
      <div class="tagline">(Tamsin Reyes)</div>
      <p>non-surgical facelift<br>first time client $99<br>only sold in series (depends on age and condition of skin)<br>series of 3 $ series of 6 $<br>series of 10 $</p>
    </article>
    <div class="divider d3"></div>

    <article class="treatment t-peel">
      <h3>50 min | micro + peel | $130</h3>
      <p>decrease fine lines &amp; wrinkles, reverses sun damage reduces scarring, rough texture, discoloration</p>
      <h3>50 min Advanced Peel | $130</h3>
      <p>Advanced peels reverse sun damage, wrinkles, acne, signs of aging</p>
    </article>
  </section>

</main>
</body>
</html>
```